Ward Compass Business Card Design*

We need a business card design for our company Ward Compass. Our company is specialized in providing online consulting services regarding medical institutions, hospitals and doctors. We work with patients worldwide looking to choose between healthcare providers. We have a website you may use as a reference, where we list doctors and clinics worldwide. So we target Medical providers as well as patients worldwide.
Target Market(s)
Medical Providers and patients around the world
Industry/Entity Type
Medical
Contact Information for Business Card
Salwa Kettani
CEO
+90 612 348 2175
info@wardcompass.example
www.wardcompass.example
14 Annakhil 7 H.R.B. Rabat, Morocco
Requirements
Must have
- Company logo/name on one full side, personal info and smaller logo and company name on the other side.
Nice to have
- Smart and elegant design

```html
<!DOCTYPE html>
<html lang="en">
<head>
<meta charset="utf-8">
<title>Ward Compass – Business Card</title>
<link rel="stylesheet" href="https://fonts.googleapis.com/css2?family=Montserrat:wght@400;700&family=Open+Sans:wght@400;700&display=swap">
<style>
  :root {
    --stage: #3b3b3d;
    --card-white: #ffffff;
    --card-shade: #eceef1;
    --navy: #13235a;
    --navy-deep: #0d1a46;
    --silver: #b5b7ba;
    --silver-line: #9a9ca0;
    --social: #3a5aa8;
    --text-light: #ffffff;
  }
  * { box-sizing: border-box; margin: 0; padding: 0; }
  html, body { width: 1200px; height: 997px; overflow: hidden; }
  body {
    background: var(--stage);
    position: relative;
    font-family: "Open Sans", Arial, sans-serif;
  }
  .card {
    position: absolute;
    width: 560px;
    height: 320px;
    background: linear-gradient(160deg, var(--card-white) 40%, var(--card-shade));
    overflow: hidden;
    box-shadow: 0 14px 30px rgba(0,0,0,.45);
  }
  .card svg.card-art { position: absolute; inset: 0; width: 100%; height: 100%; }
  .card--front { left: 60px; top: 110px; }
  .card--back { left: 580px; top: 500px; }

  .brand {
    position: absolute;
    display: flex;
    align-items: center;
    gap: 12px;
    font-family: "Montserrat", Arial, sans-serif;
    font-weight: 700;
    color: var(--navy);
    letter-spacing: 1px;
    text-transform: uppercase;
    white-space: nowrap;
    line-height: 1;
  }
  .brand-dot { border-radius: 50%; background: var(--navy); flex: none; }
  .card--front .brand { left: 60px; top: 118px; font-size: 34px; }
  .card--front .brand-dot { width: 30px; height: 30px; }
  .card--back .brand { left: 120px; top: 82px; font-size: 28px; }
  .card--back .brand-dot { width: 44px; height: 44px; }

  .tagline {
    position: absolute;
    right: 34px;
    bottom: 26px;
    font-size: 12.5px;
    line-height: 1;
    letter-spacing: 1.2px;
    color: var(--text-light);
    text-transform: uppercase;
    white-space: nowrap;
  }

  .holder {
    position: absolute;
    left: 40px;
    top: 206px;
    color: var(--text-light);
  }
  .holder-name {
    font-family: "Montserrat", Arial, sans-serif;
    font-weight: 700;
    font-size: 16px;
    line-height: 20px;
    letter-spacing: .5px;
    text-transform: uppercase;
    white-space: nowrap;
  }
  .holder-role { font-size: 12px; line-height: 15px; }

  .contact-list {
    position: absolute;
    left: 40px;
    bottom: 10px;
    list-style: none;
    color: var(--text-light);
    font-size: 13px;
    line-height: 1;
  }
  .contact-list li { display: flex; align-items: center; gap: 10px; height: 21px; white-space: nowrap; }
  .contact-icon { width: 17px; height: 17px; flex: none; }

  .social-row {
    position: absolute;
    right: 26px;
    top: 200px;
    display: flex;
    gap: 6px;
  }
  .social-dot {
    width: 18px; height: 18px;
    border-radius: 50%;
    background: var(--social);
    border: 1px solid rgba(255,255,255,.35);
  }
</style>
</head>
<body>

  <section class="card card--front" aria-label="Card front">
    <svg class="card-art" viewBox="0 0 560 320" preserveAspectRatio="none" aria-hidden="true">
      <path d="M0,320 L0,250 C140,215 260,225 360,170 C440,125 510,70 560,30 L560,320 Z" fill="var(--silver)"/>
      <path d="M0,320 L0,264 C140,232 270,240 370,186 C450,142 515,90 560,56 L560,320 Z" fill="var(--navy)"/>
      <path d="M120,228 C220,214 300,200 380,168" stroke="var(--navy-deep)" stroke-width="3" fill="none"/>
    </svg>
    <div class="brand"><span class="brand-dot"></span>Ward Compass</div>
    <p class="tagline">Find &amp; compare top rated clinics world wide</p>
  </section>

  <section class="card card--back" aria-label="Card back">
    <svg class="card-art" viewBox="0 0 560 320" preserveAspectRatio="none" aria-hidden="true">
      <path d="M0,320 L0,180 C140,150 290,180 420,160 C490,150 535,120 560,95 L560,320 Z" fill="var(--silver)"/>
      <path d="M0,320 L0,196 C140,170 290,196 420,176 C495,165 535,138 560,115 L560,320 Z" fill="var(--navy)"/>
      <path d="M340,150 C420,150 500,140 550,100" stroke="var(--silver-line)" stroke-width="4" fill="none"/>
    </svg>
    <div class="brand"><span class="brand-dot"></span>Ward Compass</div>

    <div class="holder">
      <p class="holder-name">Salwa Kettani</p>
      <p class="holder-role">CEO</p>
    </div>

    <ul class="contact-list">
      <li>
        <svg class="contact-icon" viewBox="0 0 18 18" aria-hidden="true"><circle cx="9" cy="9" r="9" fill="#fff"/><path d="M5.5 5h2l1 2.2-1.2 1a5 5 0 0 0 2.5 2.5l1-1.2 2.2 1v2c-4 .4-7.9-3.5-7.5-7.5z" fill="var(--navy)"/></svg>
        <span>+90 612 348 2175</span>
      </li>
      <li>
        <svg class="contact-icon" viewBox="0 0 18 18" aria-hidden="true"><circle cx="9" cy="9" r="9" fill="#fff"/><rect x="4.5" y="6" width="9" height="6" rx="1" fill="var(--navy)"/><path d="M5 6.5l4 3 4-3" stroke="#fff" stroke-width="1" fill="none"/></svg>
        <span>info@wardcompass.example</span>
      </li>
      <li>
        <svg class="contact-icon" viewBox="0 0 18 18" aria-hidden="true"><circle cx="9" cy="9" r="9" fill="#fff"/><circle cx="9" cy="9" r="4.5" stroke="var(--navy)" stroke-width="1.3" fill="none"/><path d="M4.5 9h9M9 4.5c-2 2.5-2 6.5 0 9M9 4.5c2 2.5 2 6.5 0 9" stroke="var(--navy)" stroke-width="1" fill="none"/></svg>
        <span>www.wardcompass.example</span>
      </li>
    </ul>

    <div class="social-row" aria-hidden="true">
      <span class="social-dot"></span>
      <span class="social-dot"></span>
      <span class="social-dot"></span>
      <span class="social-dot"></span>
      <span class="social-dot"></span>
      <span class="social-dot"></span>
    </div>
  </section>

</body>
</html>
```